Healthcare and Professional IT Services Company need a redesigned business card

We are a IT Services company that targets small medical practices and professional business such as Attorneys, Accounts, Architects etc. We want to communicate a professional yet friendly image using recent logo redesign here on ArtHarbor. Like to see the colors blue and orange in the design. Must use the Tall Pine Computing as displayed in the new logo - then also want to incorporate the fish logo as well.

Target Market(s)

Small medical and professional services

Industry/Entity Type

It Company

Contact Information for Business Card

The usual stuff, place for name address phone website. Also maybe our tagline which is "rooted in technology"

Requirements
Must have
• My new logo and the fish somewhere on the card

```html
<!DOCTYPE html>
<html lang="en">
<head>
<meta charset="utf-8">
<title>Tall Pine Computing – Business Card</title>
<link href="https://fonts.googleapis.com/css2?family=Open+Sans:wght@400;600;700&display=swap" rel="stylesheet">
<style>
  :root {
    --page-bg: #ececec;
    --card-white: #ffffff;
    --brand-blue: #1b78c1;
    --sky-blue: #27a7e1;
    --logo-blue: #2a9ad8;
    --fish-orange: #f08a4b;
    --fish-teal: #3fa9d6;
    --text-white: #ffffff;
  }
  * { box-sizing: border-box; margin: 0; padding: 0; }
  html, body {
    width: 1200px; height: 900px; overflow: hidden;
    background: var(--page-bg);
    font-family: "Open Sans", Arial, sans-serif;
  }
  .canvas { position: relative; width: 1200px; height: 900px; }

  .card {
    position: absolute; width: 556px; height: 345px; overflow: hidden;
    box-shadow: 0 6px 18px rgba(0,0,0,0.15);
  }
  .card--front { left: 240px; top: 60px; background: var(--card-white); border-radius: 0 56px 0 56px; }
  .card--back  { left: 462px; top: 518px; background: var(--sky-blue); border-radius: 56px 0 56px 0; }

  .card__band {
    position: absolute; left: 0; right: 0; top: 217px; bottom: 0;
    background: var(--brand-blue);
  }

  .fish-illustration { position: absolute; border-radius: 45% 55% 50% 50%; }
  .card--front .fish-illustration {
    left: 212px; top: 38px; width: 136px; height: 96px;
    background: radial-gradient(circle at 65% 45%, #e3f2fb, #bfe0f4);
  }
  .card--back .fish-illustration {
    left: 88px; top: 238px; width: 122px; height: 84px;
    background: linear-gradient(90deg, var(--fish-orange), var(--fish-teal) 55%, #6cc3e8);
  }

  .wordmark { position: absolute; left: 0; right: 0; text-align: center; font-weight: 700; letter-spacing: -0.5px; }
  .card--front .wordmark { top: 146px; font-size: 28px; color: var(--logo-blue); }
  .card--back .wordmark { top: 80px; font-size: 44px; color: var(--text-white); }

  .holder {
    position: absolute; right: 292px; top: 228px; text-align: right; color: var(--text-white);
  }
  .holder__name { font-size: 17px; font-weight: 700; line-height: 22px; }
  .holder__role { font-size: 14.5px; line-height: 20px; }
  .holder__address { font-size: 14.5px; line-height: 20px; margin-top: 16px; }

  .contact-list {
    position: absolute; left: 295px; top: 250px; list-style: none; color: var(--text-white);
    font-size: 14.5px; line-height: 20px;
  }
  .contact-list li { display: flex; align-items: center; gap: 6px; }
  .contact-list svg { width: 11px; height: 11px; fill: var(--text-white); flex: none; }

  .tagline {
    position: absolute; left: 232px; top: 272px; color: var(--text-white);
    font-size: 17px; font-weight: 700;
  }
</style>
</head>
<body>
<main class="canvas">

  <section class="card card--front">
    <div class="fish-illustration" role="img" aria-label="Cartoon fish mascot drawn in blue line art"></div>
    <div class="wordmark">Tall Pine Computing</div>
    <div class="card__band"></div>
    <div class="holder">
      <div class="holder__name">Daniel Reed</div>
      <div class="holder__role">Managing Director</div>
      <div class="holder__address">12345, Address Goes Here<br>Country Name, 123456.</div>
    </div>
    <ul class="contact-list">
      <li>
        <svg viewBox="0 0 12 12" aria-hidden="true"><path d="M1 4c0-2 2-3 5-3s5 1 5 3l-2 1-1-1.5H4L3 5zM2.5 6.5 4 5h4l1.5 1.5V10h-7z"/></svg>
        044-987 654 321
      </li>
      <li>
        <svg viewBox="0 0 12 12" aria-hidden="true"><path d="M1 2.5h10v7H1z M1.5 3l4.5 3.5L10.5 3" stroke="#1b78c1" stroke-width="1"/></svg>
        info@tallpine.com
      </li>
      <li>
        <svg viewBox="0 0 12 12" aria-hidden="true"><path d="M3 9l6-6" stroke="#fff" stroke-width="1.4" fill="none"/><rect x="0.8" y="6.2" width="4" height="4" rx="2" fill="none" stroke="#fff" stroke-width="1.2"/><rect x="7.2" y="1.8" width="4" height="4" rx="2" fill="none" stroke="#fff" stroke-width="1.2"/></svg>
        www.tallpine.com
      </li>
    </ul>
  </section>

  <section class="card card--back">
    <div class="wordmark">Tall Pine Computing</div>
    <div class="card__band"></div>
    <div class="fish-illustration" role="img" aria-label="Colourful cartoon fish mascot in orange and teal"></div>
    <p class="tagline">"rooted in technology"</p>
  </section>

</main>
</body>
</html>
```